Website for Torvel Capital - investment banking firm

We have a corporate identity (thanks to Ravinka/31842) and want to extend that into a website design.  See the attached zipped files.
We have software folks in-house to do the coding.
See the attached Project Brief & Notes for more details.  Don't worry about the actual text - lorem ipsum will be fine.
The server will be Apache.
Thank you!
Desmond

Industry/Entity Type
Investment

```html
<!DOCTYPE html>
<html lang="en">
<head>
<meta charset="utf-8">
<title>Torvel Capital</title>
<link href="https://fonts.googleapis.com/css2?family=Cinzel:wght@500;600&family=Mulish:wght@400;600;700&display=swap" rel="stylesheet">
<style>
:root{
  --navy:#1f4b8e;
  --sky:#3b97c4;
  --ink:#3a3a3a;
  --muted:#666;
  --line:#d0d0d0;
  --footer:#ebebeb;
  --tile-a:#dfe7ee;
  --tile-b:#b9ccd9;
}
*{margin:0;padding:0;box-sizing:border-box}
html,body{width:1200px;height:1125px;overflow:hidden;background:#fff}
body{font-family:"Mulish",Arial,sans-serif;color:var(--ink);position:relative}
a{color:inherit;text-decoration:none}
.abs{position:absolute}

/* header */
.brand{left:118px;top:30px;display:flex;align-items:center;gap:14px}
.brand-mark{width:50px;height:50px;background:var(--navy);border-radius:50%}
.brand-name{font-size:29px;font-weight:600;color:var(--navy);letter-spacing:.5px}
.util-nav{top:17px;left:524px;font-size:13px;color:#555;display:flex;gap:14px}
.util-nav span.sep{color:#777}
.login{left:803px;top:0;width:83px;height:38px;background:var(--navy);color:#fff;font-size:14px;display:flex;align-items:center;justify-content:center}
.search{left:897px;top:12px;width:178px;height:27px;border:1px solid var(--line);display:flex}
.search span{flex:1;font-size:13px;color:#999;padding:4px 8px}
.search b{width:26px;background:#9a9a9a;display:flex;align-items:center;justify-content:center}
.main-nav{top:68px;font-size:14px;color:#444}
.main-nav a{position:absolute;white-space:nowrap}

/* hero */
.hero-bg{left:0;top:128px;width:1200px;height:510px;background:linear-gradient(180deg,var(--tile-a) 0%,var(--tile-b) 55%,#eef2f5 70%,#fafbfc 100%)}
.hero{left:120px;top:128px;width:960px;height:404px;background:linear-gradient(90deg,#f7f8f6 0%,#eef0ec 35%,#c9c6c0 60%,#d8d3cc 80%,#b9b6b2 100%)}
.hero-title{left:147px;top:214px;font-family:"Cinzel",Georgia,serif;font-weight:600;font-size:41px;line-height:44px;color:#222;letter-spacing:1px}
.hero-sub{left:147px;top:312px;font-size:16.5px;line-height:26px;color:#666}
.hero-btn{left:146px;top:383px;width:139px;height:41px;border:2px solid var(--navy);color:var(--navy);font-size:16px;display:flex;align-items:center;justify-content:center}
.dots{left:153px;top:486px;display:flex;gap:8px}
.dots i{width:9px;height:9px;border-radius:50%;background:#999}
.dots i:first-child{background:var(--sky)}

/* service tiles */
.tiles{left:120px;top:532px;width:960px;height:166px;display:flex}
.tile{width:240px;padding:12px 20px;color:#fff;position:relative}
.tile:nth-child(odd){background:var(--navy)}
.tile:nth-child(even){background:var(--sky)}
.tile h3{font-weight:600;font-size:18px;line-height:25px;letter-spacing:.5px}
.tile p{font-size:13.5px;line-height:22px;margin-top:14px;letter-spacing:.2px}
.tile svg{position:absolute;right:18px;top:16px}

/* columns */
.col h2{font-size:19px;font-weight:600;color:#333;letter-spacing:.3px}
.col p{font-size:13.5px;line-height:25px;color:var(--muted)}
.more{font-size:12.5px;color:var(--navy);border-bottom:1px solid var(--navy);letter-spacing:.4px}
.photo{border:1px solid #c8c8c8}
.news-title{font-size:14.5px;font-weight:700;color:var(--navy);letter-spacing:.3px}
.news-text{font-size:13.5px;line-height:23px;color:var(--muted)}
.news-date{font-size:13.5px;color:#555}

/* footer */
.footer{left:0;top:1059px;width:1200px;height:66px;background:var(--footer);font-size:13px;color:#555}
.footer-links{position:absolute;left:136px;top:23px;display:flex;gap:20px}
.copyright{position:absolute;right:137px;top:24px}
</style>
</head>
<body>

<header>
  <div class="abs brand"><span class="brand-mark"></span><span class="brand-name">Torvel Capital</span></div>
  <nav class="abs util-nav"><a>Investor Relations</a><span class="sep">/</span><a>Locations</a><span class="sep">/</span><a>News</a></nav>
  <a class="abs login">Login</a>
  <div class="abs search"><span>enter search term</span><b><svg width="9" height="10" viewBox="0 0 9 10"><path d="M1 0l8 5-8 5z" fill="#fff"/></svg></b></div>
  <nav class="abs main-nav">
    <a style="left:492px">Home</a>
    <a style="left:569px">About</a>
    <a style="left:647px">Services</a>
    <a style="left:740px">Current Engagements</a>
    <a style="left:919px">Completed Transactions</a>
  </nav>
</header>

<section>
  <div class="abs hero-bg" role="img" aria-label="Soft pale blue tiled backdrop"></div>
  <div class="abs hero" role="img" aria-label="Photo of a smiling couple meeting with an advisor"></div>
  <h1 class="abs hero-title">A Bank of<br>Investment</h1>
  <p class="abs hero-sub">One of the Leading Dallas-based Private<br>Investment Banking Advisory Firm!</p>
  <a class="abs hero-btn">READ MORE</a>
  <div class="abs dots"><i></i><i></i><i></i></div>
</section>

<section class="abs tiles">
  <div class="tile">
    <h3>Strategic<br>Advisory</h3>
    <svg width="46" height="44" viewBox="0 0 46 44" fill="none" stroke="#fff" stroke-width="3"><path d="M4 38l12-12 8 7 16-18"/><path d="M32 14h9v9"/></svg>
    <p>Lorem Ipsum is simply dummy text of the printing and typ setting industry.</p>
  </div>
  <div class="tile">
    <h3>Current<br>Engagement</h3>
    <svg width="48" height="40" viewBox="0 0 48 40" fill="none" stroke="#fff" stroke-width="3"><path d="M12 6a16 16 0 0 0 0 28"/><path d="M36 6a16 16 0 0 1 0 28"/><text x="24" y="27" fill="#fff" stroke="none" font-size="20" font-weight="700" text-anchor="middle" font-family="Mulish,sans-serif">$</text></svg>
    <p>Lorem Ipsum is simply dummy text of the printing and typ setting industry.</p>
  </div>
  <div class="tile">
    <h3>Completed<br>Transactions</h3>
    <svg width="42" height="38" viewBox="0 0 42 38" fill="none" stroke="#fff" stroke-width="3"><rect x="2" y="4" width="38" height="32"/><path d="M10 20l8 8 16-16"/></svg>
    <p>Lorem Ipsum is simply dummy text of the printing and typ setting industry.</p>
  </div>
  <div class="tile">
    <h3>Regulatory<br>Complaince</h3>
    <svg width="36" height="38" viewBox="0 0 36 38" fill="none" stroke="#fff" stroke-width="3"><path d="M6 2v34M18 2v34M30 2v34"/><rect x="2" y="22" width="8" height="6" fill="var(--sky)"/><rect x="14" y="8" width="8" height="6" fill="var(--sky)"/><rect x="26" y="18" width="8" height="6" fill="var(--sky)"/></svg>
    <p>Lorem Ipsum is simply dummy text of the printing and typ setting industry.</p>
  </div>
</section>

<section>
  <div class="abs col" style="left:135px;top:730px;width:335px">
    <h2>Our Company</h2>
    <div class="photo" role="img" aria-label="Photo of a business team standing in an office" style="margin-top:24px;width:332px;height:138px;background:linear-gradient(90deg,#c9ccd0,#8d96a3 40%,#e4e6e8 60%,#7f8894)"></div>
    <p style="margin-top:12px;padding-left:2px">Lorem Ipsum is simply dummy text of the printing and typesetting industry. Lorem Ipsum has been</p>
  </div>
  <a class="abs more" style="left:137px;top:994px">READ MORE</a>

  <div class="abs col" style="left:494px;top:730px;width:310px">
    <h2>Latest News</h2>
  </div>
  <div class="abs news-title" style="left:494px;top:776px">Lorem Ipsum Dolor Sit amet and entering</div>
  <div class="abs news-text" style="left:494px;top:801px;width:305px">Lorem Ipsum is simply dummy text of the print-<br>ing and typesetting industry.</div>
  <div class="abs news-date" style="left:494px;top:861px">02/07/14</div>
  <div class="abs news-title" style="left:494px;top:897px">Lorem Ipsum Dolor Sit amet and entering.</div>
  <div class="abs news-text" style="left:494px;top:922px">Lorem Ipsum is simply dummy text of the print</div>
  <div class="abs news-date" style="left:494px;top:957px">02/07/14</div>
  <a class="abs more" style="left:494px;top:994px">VIEW ALL</a>

  <div class="abs col" style="left:828px;top:730px;width:240px">
    <h2>Our Global Network</h2>
    <div class="photo" role="img" aria-label="World map highlighting the Asia/Pacific region" style="margin-top:24px;margin-left:2px;width:231px;height:136px;background:linear-gradient(90deg,#e3ebf2,#2a4d7e 30%,#2a4d7e 60%,#3f9fd0 80%,#e3ebf2)"></div>
    <p style="margin-top:10px;padding-left:2px">Lorem Ipsum is simply dummy text of the printing and typesetting</p>
  </div>
  <a class="abs more" style="left:828px;top:994px">READ MORE</a>
</section>

<footer class="abs footer">
  <nav class="footer-links"><a>Home</a><a>Terms &amp; Conditions</a><a>Contact Us</a></nav>
  <div class="copyright">© 2014 Torvel Capital. All Rights Reserved</div>
</footer>

</body>
</html>
```